MRT Property - Business Cards

Looking for a business card & general letterhead, signage etc design for our new logo.

Colours:
000a20
0056a2
00b5ef
0088ce
68cef2

Fonts:
Poppins
Karla

Please keep look and feel of new brand - example in the zip package I sent.

```html
<!DOCTYPE html>
<html lang="en">
<head>
<meta charset="utf-8">
<title>MRT Property – Business Cards</title>
<link rel="stylesheet" href="https://fonts.googleapis.com/css2?family=Poppins:wght@400;600;700&family=Karla:wght@400;500&display=swap">
<style>
  :root {
    --ink: #000a20;
    --navy: #0056a2;
    --sky: #00b5ef;
    --ocean: #0088ce;
    --mist: #68cef2;
    --paper: #fafafa;
    --grey: #5a5f66;
    --stage: #14161a;
  }
  * { box-sizing: border-box; margin: 0; padding: 0; }
  html, body { width: 1200px; height: 963px; overflow: hidden; }
  body {
    background: var(--stage);
    display: flex;
    flex-direction: column;
    align-items: center;
    justify-content: center;
    gap: 60px;
  }
  .card {
    width: 640px;
    height: 366px;
    border-radius: 22px;
    position: relative;
    overflow: hidden;
    box-shadow: 0 18px 40px rgba(0, 0, 0, 0.55);
  }

  /* Front */
  .card--front { background: var(--paper); padding: 38px 44px; }
  .brand-name {
    font-family: "Poppins", sans-serif;
    font-weight: 700;
    font-size: 44px;
    line-height: 1;
    letter-spacing: 1px;
    color: var(--navy);
  }
  .holder { margin-top: 34px; }
  .holder__name {
    font-family: "Poppins", sans-serif;
    font-weight: 700;
    font-size: 22px;
    color: var(--sky);
    letter-spacing: 0.5px;
  }
  .holder__role {
    font-family: "Karla", sans-serif;
    font-size: 16px;
    color: var(--grey);
    margin-top: 2px;
  }
  .address {
    font-family: "Karla", sans-serif;
    font-size: 16px;
    line-height: 1.35;
    color: var(--grey);
    margin-top: 18px;
  }
  .contact { list-style: none; margin-top: 16px; }
  .contact__item {
    display: flex;
    align-items: center;
    gap: 10px;
    font-family: "Karla", sans-serif;
    font-size: 16px;
    line-height: 1.5;
    color: var(--grey);
  }
  .contact__icon { width: 14px; height: 14px; flex: none; }

  /* Back */
  .card--back {
    background: linear-gradient(160deg, var(--mist) 0%, var(--sky) 40%, var(--ocean) 75%, var(--navy) 100%);
    display: flex;
    align-items: center;
    justify-content: center;
  }
  .card--back .brand-name {
    color: #ffffff;
    font-size: 58px;
  }
</style>
</head>
<body>
  <section class="card card--front" aria-label="Business card front">
    <div class="brand-name">MRT PROPERTY</div>
    <div class="holder">
      <div class="holder__name">DANIEL CARTER</div>
      <div class="holder__role">Manager</div>
    </div>
    <div class="address">48 Harbour Lane, Easton<br>Region, Zip 4021</div>
    <ul class="contact">
      <li class="contact__item">
        <svg class="contact__icon" viewBox="0 0 24 24" aria-hidden="true"><path fill="#0088ce" d="M6.6 10.8a15.1 15.1 0 0 0 6.6 6.6l2.2-2.2a1 1 0 0 1 1-.25 11.4 11.4 0 0 0 3.6.57 1 1 0 0 1 1 1V20a1 1 0 0 1-1 1A17 17 0 0 1 3 4a1 1 0 0 1 1-1h3.5a1 1 0 0 1 1 1c0 1.25.2 2.45.57 3.6a1 1 0 0 1-.25 1z"/></svg>
        555-018-7342
      </li>
      <li class="contact__item">
        <svg class="contact__icon" viewBox="0 0 24 24" aria-hidden="true"><rect x="2.5" y="5" width="19" height="14" rx="1.5" fill="none" stroke="#0088ce" stroke-width="2"/><path d="M3 6l9 7 9-7" fill="none" stroke="#0088ce" stroke-width="2"/></svg>
        hello@mrtmail.com
      </li>
      <li class="contact__item">
        <svg class="contact__icon" viewBox="0 0 24 24" aria-hidden="true"><g fill="none" stroke="#0088ce" stroke-width="2"><circle cx="12" cy="12" r="9.5"/><ellipse cx="12" cy="12" rx="4" ry="9.5"/><path d="M2.5 12h19M4 7h16M4 17h16"/></g></svg>
        www.mrtpropertyweb.com
      </li>
    </ul>
  </section>

  <section class="card card--back" aria-label="Business card back">
    <div class="brand-name">MRT PROPERTY</div>
  </section>
</body>
</html>
```